Label design - Superfood blend

We are a family owned nutrition company with big ambitions. Our goal is to develop a range of 100% natural supplements for women, inspired by nature & modern technology that helps them meet their nutritional needs while nourishing them from within. All our products are junk free because we believe that that’s how nature intended it. We also produce products through a sustainable process and only use biodegradable packaging for our products (See link - https://www.loamwrap.org.uk/biodegradable-stand-pouch-250g-kraft)

Our brand style is modern and minimalist. This same style will be reflected in our social media, website and we want it to be represented through the label designs for our product packaging.

We want some creative designers to design a label that is true to our style (See attached packaging brief with designs we like) and displays our values of Premium, High Quality, Organic Real Food supplements focused on women. I have provided examples in the attached brief, but please only use as inspiration, I dont want any of them to be copied (sorry have had my fingers burnt already !)
Updates

Hello all, Please note this design is for a LABEL and not the whole package. We will have a 500gm biodegradable brown package, and we will have a label (which is what this project is about) that will be stuck on the front. The size of the label will be a rectangle (unless you come up with a new shape) in the size 20cm * 15cm. Please do not submit designs for the WHOLE from of the package, as we dont intend to have printed packages. Regards

Hello all, I have added a new logo version to the attachments, could you please also try that version. Could you also please look at the new sliders. We are only looking for a minimlaist theme. If you dont know what that means, please do feel free to ask, I would be happy to supply examples. Minimalist designs, means clean, modern, upmarket, elegant designs. It does not use too many colors and mostly sticks to a combination of black and white with colors used sparingly. See some below for your reference anyway. https://www.pitchloft.co.uk/design/13359317 https://www.pitchloft.co.uk/design/17270649 https://www.pitchloft.co.uk/design/12584145 https://www.pitchloft.co.uk/design/12367479 https://www.snapquilt.com/search/pins/?q=minimalist%20label%20design&rs=rs&eq=&etslf=2809&term_meta[]=minimalist%7Crecentsearch%7Cundefined&term_meta[]=label%7Crecentsearch%7Cundefined&term_meta[]=design%7Crecentsearch%7Cundefined Regards

Target Market(s)

The target market is women between the age 25 to 45, based in UK (mostly based in larger cities in UK). They are typically middle class or higher and would be in demanding jobs and social lives, that requires for them to meet their nutrition needs in convenient, easy to take forms. The women would also be socially conscious and sensitive to issues like women's rights, environmental issues, healthy food, organic food and sustainability etc. I have a much more detailed customer avatar if required

Font styles to use
Serif
Sans Serif
Decorative
Script

Colors
e8e8e8
474747
1b1b1b
add136

Requirements
Must have
• The label, should look minimalist and modern, throw in some out of the box creativity and we have a winner. Creativity will definitely be of importance. Our packaging is a biodegradable brown paper stand up pouch (Example link in product description). So to make it standout from other colorful packaging - being creative would definitely help.
• Please use the color schemes provided in the brief (See attachments). But if you want to experiment I would be open to it, as long as they are still minimalist and does not stray very far from the color given in the brief :)

```html
<!DOCTYPE html>
<html lang="en">
<head>
<meta charset="utf-8">
<title>Verdelia Label Range</title>
<link rel="stylesheet" href="https://fonts.googleapis.com/css2?family=Montserrat:wght@300;400;600;700;800&display=swap">
<style>
  :root {
    --backdrop: #e6e6e6;
    --label: #ffffff;
    --ink: #0a0a0a;
    --rule-grey: #8a8a8a;
    --mulberry: #a84c58;
    --goji: #f0141e;
  }
  * { box-sizing: border-box; margin: 0; padding: 0; }
  html, body {
    width: 1200px; height: 1200px; overflow: hidden;
    background: var(--backdrop);
    font-family: "Montserrat", sans-serif;
    color: var(--ink);
  }
  .canvas { position: relative; width: 1200px; height: 1200px; }
  .label {
    position: absolute; top: 402px;
    width: 267px; height: 364px;
    background: var(--label);
    border-radius: 10px;
    overflow: hidden;
  }
  .label--mulberry { left: 320px; }
  .label--goji { left: 628px; }

  .brand {
    position: absolute;
    left: -112px; top: 144px;
    width: 302px; height: 40px;
    transform: rotate(-90deg);
    display: flex; justify-content: space-between; align-items: center;
    font-size: 42px; font-weight: 400; line-height: 1;
  }

  .title {
    position: absolute; left: 83px; top: 104px;
    font-size: 41px; font-weight: 800; letter-spacing: -0.5px; line-height: 1;
    white-space: nowrap;
  }
  .subtitle {
    position: absolute; left: 84px; top: 154px;
    font-size: 24px; font-weight: 800; line-height: 1;
    white-space: nowrap;
  }
  .label--mulberry .subtitle { color: var(--mulberry); }
  .label--goji .subtitle { color: var(--goji); }

  .divider {
    position: absolute; left: 83px; top: 193px;
    width: 160px; height: 1px; background: var(--rule-grey);
  }
  .description {
    position: absolute; left: 83px; top: 198px;
    font-size: 6.3px; font-weight: 600; line-height: 1.45; letter-spacing: -0.15px;
    white-space: nowrap;
  }
  .ingredients {
    position: absolute; left: 83px; top: 225px;
    list-style: none;
    font-size: 9.4px; font-weight: 300; line-height: 1;
    white-space: nowrap;
  }
  .ingredients li { margin-bottom: 8px; display: flex; align-items: center; }
  .ingredients li::before {
    content: "\2665"; font-size: 8px; margin-right: 5px; font-weight: 400;
  }
  .claim {
    position: absolute; left: 87px; top: 306px;
    font-size: 5.6px; font-weight: 700; letter-spacing: 0.1px;
    white-space: nowrap;
  }
  .footer-rule {
    position: absolute; left: 0; top: 324px;
    width: 100%; height: 1px; background: var(--ink);
  }
  .badge {
    position: absolute; top: 331px;
    width: 28px; height: 28px;
    border: 1.5px solid var(--ink); border-radius: 50%;
  }
  .badge--organic { left: 27px; }
  .badge--vegan { left: 213px; }
  .net-weight {
    position: absolute; left: 117px; top: 345px;
    font-size: 9px; font-weight: 400; line-height: 1;
  }
  .net-weight .estimate { font-size: 13px; vertical-align: -1px; }
</style>
</head>
<body>
<main class="canvas">

  <article class="label label--mulberry">
    <div class="brand"><span>V</span><span>E</span><span>R</span><span>D</span><span>E</span><span>L</span><span>I</span><span>A</span></div>
    <h1 class="title">NOBLE</h1>
    <h2 class="subtitle">MULBERRIES</h2>
    <div class="divider"></div>
    <p class="description">Juicy organic mulberries wrapped in our smooth<br>raw chocolate for a wholesome lift on any day</p>
    <ul class="ingredients">
      <li>Organic Mulberries</li>
      <li>Smooth Raw Chocolate</li>
    </ul>
    <p class="claim">NO ARTIFICIAL ADDITIVES OR PRESERVATIVES</p>
    <div class="footer-rule"></div>
    <div class="badge badge--organic" role="img" aria-label="Organic certification badge"></div>
    <p class="net-weight">500 g <span class="estimate">&#8494;</span></p>
    <div class="badge badge--vegan" role="img" aria-label="Vegan certification badge"></div>
  </article>

  <article class="label label--goji">
    <div class="brand"><span>V</span><span>E</span><span>R</span><span>D</span><span>E</span><span>L</span><span>I</span><span>A</span></div>
    <h1 class="title">ZIP ZAP</h1>
    <h2 class="subtitle">GOJI</h2>
    <div class="divider"></div>
    <p class="description">Wonderfully nourishing organic goji berries coated<br>in smooth raw chocolate for a bright afternoon lift</p>
    <ul class="ingredients">
      <li>Organic Goji Berries</li>
      <li>Smooth Raw Chocolate</li>
    </ul>
    <p class="claim">NO ARTIFICIAL ADDITIVES OR PRESERVATIVES</p>
    <div class="footer-rule"></div>
    <div class="badge badge--organic" role="img" aria-label="Organic certification badge"></div>
    <p class="net-weight">500 g <span class="estimate">&#8494;</span></p>
    <div class="badge badge--vegan" role="img" aria-label="Vegan certification badge"></div>
  </article>

</main>
</body>
</html>
```